Business Card Design

We need a design for business cards for our company. We have a logo. We teach EMT's and we are based out of Virginia. The information that will need to add would be, name, title, phone number, email, address. On the back of the business card would be "We help you, help others"

Target Market(s)

People that want to become EMT's

Colors

Designer to choose colors to be used in the design.

Requirements
Must have
• company logo

```html
<!DOCTYPE html>
<html lang="en">
<head>
<meta charset="UTF-8">
<title>Ridgeline Medic Academy – Business Cards</title>
<link href="https://fonts.googleapis.com/css2?family=Montserrat:wght@400;500;700&display=swap" rel="stylesheet">
<style>
  :root {
    --page-bg: #2b2f33;
    --card-navy: #1f2b36;
    --accent-red: #c81e32;
    --text-light: #d9dde2;
    --text-muted: #9aa4ae;
    --divider: #6b7580;
  }
  * { box-sizing: border-box; margin: 0; padding: 0; }
  html, body {
    width: 1200px;
    height: 900px;
    overflow: hidden;
    background: var(--page-bg);
    font-family: "Montserrat", sans-serif;
  }
  .sheet {
    width: 1200px;
    height: 900px;
    display: flex;
    align-items: center;
    justify-content: center;
    gap: 40px;
  }
  .card {
    position: relative;
    width: 540px;
    height: 309px;
    background: var(--card-navy);
    border-radius: 4px;
    box-shadow: 0 18px 40px rgba(0,0,0,0.45);
    overflow: hidden;
  }
  .brand {
    display: flex;
    align-items: center;
    gap: 10px;
  }
  .brand-dot {
    width: 14px;
    height: 14px;
    border-radius: 50%;
    background: var(--accent-red);
    flex-shrink: 0;
  }
  .brand-name {
    font-weight: 700;
    color: var(--accent-red);
    text-transform: uppercase;
    letter-spacing: 0.5px;
    line-height: 1.1;
  }

  /* Contact side */
  .card-front {
    display: flex;
    align-items: center;
    padding: 0 40px;
  }
  .card-front .brand { width: 210px; }
  .card-front .brand-name { font-size: 19px; }
  .card-divider {
    width: 1px;
    height: 90px;
    background: var(--divider);
    margin: 0 26px 0 14px;
  }
  .contact { color: var(--text-light); }
  .contact-name {
    color: var(--accent-red);
    font-weight: 700;
    font-size: 19px;
    text-transform: uppercase;
    letter-spacing: 0.5px;
  }
  .contact-title {
    font-size: 14px;
    color: var(--text-muted);
    margin: 2px 0 12px;
  }
  .contact-line {
    display: flex;
    align-items: center;
    gap: 8px;
    font-size: 14px;
    margin-top: 5px;
  }
  .contact-line svg { width: 13px; height: 13px; flex-shrink: 0; }

  /* Tagline side */
  .card-back .brand {
    position: absolute;
    top: 80px;
    left: 0;
    right: 0;
    justify-content: center;
  }
  .card-back .brand-name { font-size: 26px; }
  .tagline-band {
    position: absolute;
    left: 0;
    right: 0;
    bottom: 0;
    height: 70px;
    background: var(--accent-red);
    display: flex;
    align-items: center;
    justify-content: center;
  }
  .tagline {
    color: #ffffff;
    font-weight: 700;
    font-size: 15px;
    letter-spacing: 3px;
    text-transform: uppercase;
  }
</style>
</head>
<body>
  <main class="sheet">
    <section class="card card-front">
      <div class="brand">
        <span class="brand-dot"></span>
        <span class="brand-name">Ridgeline Medic Academy</span>
      </div>
      <div class="card-divider"></div>
      <div class="contact">
        <div class="contact-name">Daniel Reyes</div>
        <div class="contact-title">Sales Manager</div>
        <div class="contact-line">
          <svg viewBox="0 0 16 16" fill="none" stroke="currentColor" stroke-width="1.3">
            <circle cx="8" cy="8" r="7"/>
            <path d="M5.5 4.5l1.5 0 .7 1.8-1 .8a5 5 0 0 0 2.2 2.2l.8-1 1.8.7v1.5a1 1 0 0 1-1 1A6 6 0 0 1 4.5 5.5a1 1 0 0 1 1-1z"/>
          </svg>
          <span>555-013-2468</span>
        </div>
        <div class="contact-line">
          <svg viewBox="0 0 16 16" fill="none" stroke="currentColor" stroke-width="1.3">
            <rect x="1.5" y="3.5" width="13" height="9"/>
            <path d="M1.5 3.5l6.5 5 6.5-5"/>
          </svg>
          <span>hello@ridgelinemedic.com</span>
        </div>
      </div>
    </section>

    <section class="card card-back">
      <div class="brand">
        <span class="brand-dot"></span>
        <span class="brand-name">Ridgeline Medic Academy</span>
      </div>
      <div class="tagline-band">
        <p class="tagline">We help you, help others</p>
      </div>
    </section>
  </main>
</body>
</html>
```